Freelance business trainer needs a new business card

My business is called Brontlearn. I provide training in the workplace on management, coaching and mentoring, and customer service topics for a variety of businesses, colleges and private training providers, and teach on management programs. I need a professional but eye catching business card. Business colours grey and orange. My name Marion Tadwick; Tel 07382 415067; email mtadwick@brontlearn.co.uk; website www.brontlearn.co.uk.
Happy to have some sort of logo on front and details on back or all on one side
Target Market(s)
SME businesses and colleges - workshops i run are for adults in the workplace
Industry/Entity Type
Training
Look and feel

```html
<!DOCTYPE html>
<html lang="en">
<head>
<meta charset="utf-8">
<title>Brontlearn – Business Card</title>
<link rel="stylesheet" href="https://fonts.googleapis.com/css2?family=Cinzel:wght@400;600&family=Gelasio:wght@400&display=swap">
<style>
  :root {
    --frame-grey: #4b5b5d;
    --edge-grey: #5a6b6e;
    --steel-light: #7f8f91;
    --steel-dark: #1c2526;
    --orange-deep: #f23a00;
    --orange-bright: #ff8c00;
    --accent-yellow: #ffd200;
    --ink: #0d0d0d;
  }
  html, body {
    margin: 0;
    padding: 0;
    overflow: hidden;
    background: #ffffff;
  }
  .card {
    position: relative;
    width: 1200px;
    height: 720px;
    overflow: hidden;
  }
  .card-art {
    position: absolute;
    inset: 0;
    display: block;
  }
  .brand {
    position: absolute;
    left: 105px;
    top: 112px;
    display: flex;
    align-items: center;
    gap: 26px;
  }
  .brand-mark {
    width: 84px;
    height: 84px;
    background: var(--accent-yellow);
  }
  .brand-name {
    font-family: "Cinzel", serif;
    font-weight: 600;
    font-size: 64px;
    color: var(--ink);
    letter-spacing: 1px;
  }
  .person-name {
    position: absolute;
    left: 68px;
    top: 300px;
    margin: 0;
    font-family: "Cinzel", serif;
    font-weight: 400;
    font-size: 76px;
    line-height: 1;
    color: var(--ink);
    letter-spacing: 1px;
  }
  .contact-list {
    position: absolute;
    left: 68px;
    top: 448px;
    margin: 0;
    padding: 0;
    list-style: none;
  }
  .contact-item {
    display: flex;
    align-items: center;
    height: 57px;
    font-family: "Gelasio", serif;
    font-size: 32px;
    color: var(--ink);
    letter-spacing: 1px;
  }
  .contact-icon {
    width: 50px;
    height: 40px;
    margin-right: 14px;
    flex: none;
  }
</style>
</head>
<body>
<main class="card">
  <svg class="card-art" width="1200" height="720" viewBox="0 0 1200 720" aria-hidden="true">
    <defs>
      <radialGradient id="steelSweep" cx="1180" cy="380" r="520" gradientUnits="userSpaceOnUse">
        <stop offset="0" stop-color="var(--steel-light)"/>
        <stop offset="1" stop-color="var(--steel-dark)"/>
      </radialGradient>
      <linearGradient id="orangeFill" x1="0" y1="0" x2="0" y2="1">
        <stop offset="0" stop-color="var(--orange-deep)"/>
        <stop offset="0.5" stop-color="var(--orange-bright)"/>
        <stop offset="1" stop-color="var(--orange-deep)"/>
      </linearGradient>
    </defs>
    <rect class="frame" width="1200" height="720" fill="var(--frame-grey)"/>
    <path class="steel-corner" d="M1200 320 V720 H520 C860 680 1110 540 1200 320 Z" fill="url(#steelSweep)"/>
    <path class="curve-edge" d="M1184 340 C1100 530 860 672 555 706" fill="none" stroke="var(--edge-grey)" stroke-width="22"/>
    <path class="orange-panel" d="M16 16 H1184 V336 C1100 520 850 660 540 704 H16 Z" fill="url(#orangeFill)"/>
  </svg>

  <div class="brand">
    <span class="brand-mark"></span>
    <span class="brand-name">Brontlearn</span>
  </div>

  <h1 class="person-name">Marion Tadwick</h1>

  <ul class="contact-list">
    <li class="contact-item">
      <svg class="contact-icon" viewBox="0 0 50 40" aria-hidden="true">
        <path d="M8 4 L15 2 L19 12 L14 15 C16 22 20 27 26 30 L30 25 L39 30 L36 38 C22 38 9 24 8 4 Z" fill="var(--accent-yellow)"/>
      </svg>
      <span>07382 415067</span>
    </li>
    <li class="contact-item">
      <svg class="contact-icon" viewBox="0 0 50 40" aria-hidden="true">
        <g fill="none" stroke="var(--accent-yellow)" stroke-width="3">
          <circle cx="24" cy="20" r="17"/>
          <ellipse cx="24" cy="20" rx="7" ry="17"/>
          <line x1="7" y1="20" x2="41" y2="20"/>
          <line x1="24" y1="3" x2="24" y2="37"/>
          <path d="M10 11 H38 M10 29 H38"/>
        </g>
      </svg>
      <span>www.brontlearn.co.uk</span>
    </li>
    <li class="contact-item">
      <svg class="contact-icon" viewBox="0 0 50 40" aria-hidden="true">
        <rect x="2" y="9" width="42" height="24" fill="var(--accent-yellow)"/>
        <path d="M2 9 L23 24 L44 9" fill="none" stroke="var(--orange-bright)" stroke-width="2"/>
      </svg>
      <span>mtadwick@brontlearn.co.uk</span>
    </li>
  </ul>
</main>
</body>
</html>
```